Banner ads for LP that work with same theme as below banners

Love the banner ads below. Need more with attached photos. But use the same wording, font as in below banner ads. Should be LP size 1200/627 so I can use for Pixorly and LP. Looking for great ads to use as LP ads. We do lots of ads so it will be worth your time to enter this contest you will be rewarded with a ton of work. Need several banner ads that work together. So maybe 1 of the dresses, 1 of the sweater, 1 of the leggings, 1 of the jacket

Target Market(s)

Women 24-45

Industry/Entity Type

Fashion

Requirements
Must have
• Banner ads that work for LP and Pixorly
Nice to have
• Several options to choose from
Should not have
• not sure

```html
<!DOCTYPE html>
<html lang="en">
<head>
<meta charset="UTF-8">
<title>Winter Wear Collection</title>
<link rel="stylesheet" href="https://fonts.googleapis.com/css2?family=Playball&family=Playfair+Display:wght@700;900&family=Libre+Baskerville:wght@700&display=swap">
<style>
  :root {
    --damask-light: #e9e4d8;
    --damask-mid: #cfc7b4;
    --badge: #c5bca8;
    --ink: #3d332b;
    --wine: #7a1f3f;
    --button: #4f4538;
    --button-text: #f4efe6;
    --ring: #a79e8c;
    --photo-top: #c9c0ad;
    --jacket-dark: #2a2b30;
    --jacket-navy: #2c3f60;
    --knit-grey: #9a9893;
  }
  html, body {
    margin: 0;
    padding: 0;
    width: 1200px;
    height: 627px;
    overflow: hidden;
  }
  .banner {
    position: relative;
    width: 1200px;
    height: 627px;
    overflow: hidden;
  }
  .damask-background {
    position: absolute;
    inset: 0;
    background: radial-gradient(ellipse at 60% 45%, var(--damask-light) 0%, var(--damask-mid) 100%);
  }
  .model-ring {
    position: absolute;
    left: 0;
    top: 0;
  }
  .model-photo {
    position: absolute;
    left: 95px;
    top: 82px;
    width: 480px;
    height: 480px;
    border-radius: 50%;
    background: linear-gradient(180deg, var(--photo-top) 0%, var(--jacket-navy) 30%, var(--jacket-dark) 60%, var(--knit-grey) 80%, var(--jacket-dark) 100%);
  }
  .offer-badge {
    position: absolute;
    left: 685px;
    top: 163px;
    width: 440px;
    height: 440px;
    border-radius: 50%;
    background: var(--badge);
  }
  .headline-script {
    position: absolute;
    left: 685px;
    width: 440px;
    top: 282px;
    margin: 0;
    text-align: center;
    font-family: "Playball", cursive;
    font-weight: 400;
    font-size: 52px;
    letter-spacing: 4px;
    color: var(--ink);
    line-height: 1;
  }
  .headline-main {
    position: absolute;
    left: 685px;
    width: 440px;
    top: 334px;
    margin: 0;
    text-align: center;
    font-family: "Playfair Display", serif;
    font-weight: 900;
    font-size: 62px;
    color: var(--wine);
    line-height: 1;
    transform: scaleX(0.85);
    transform-origin: center;
  }
  .shop-button {
    position: absolute;
    left: 792px;
    top: 432px;
    width: 226px;
    height: 58px;
    background: var(--button);
    color: var(--button-text);
    display: flex;
    align-items: center;
    justify-content: center;
    font-family: "Libre Baskerville", serif;
    font-weight: 700;
    font-size: 14px;
    letter-spacing: 2.5px;
    text-decoration: none;
  }
</style>
</head>
<body>
  <div class="banner">
    <div class="damask-background" role="img" aria-label="Light beige and cream damask scroll pattern"></div>

    <svg class="model-ring" width="1200" height="627" viewBox="0 0 1200 627" aria-hidden="true">
      <circle cx="337" cy="322" r="252" fill="none" stroke="var(--ring)" stroke-width="1"/>
    </svg>

    <div class="model-photo" role="img" aria-label="Two models wearing quilted puffer jackets, one navy and one black, with faux fur hoods and grey cable-knit hems"></div>

    <div class="offer-badge"></div>
    <h2 class="headline-script">Winter Wear</h2>
    <h1 class="headline-main">COLLECTION</h1>
    <a class="shop-button" href="#">SHOP THE LOOK</a>
  </div>
</body>
</html>
```